Natural Light/Organic/Documentary Photography Business

I like a simple, approachable, feminine, earthy/organic feel. Earth/neutral tones, nothing too loud or obnoxious. I like the watercolor look. I don't want anything too trendy or something I'll get tired of after a couple months. As far as colors, I am much more a fan of cream/taupe/blue/green...not a fan of pink or purple at all.

Target Market(s)

Weddings & Families

Industry/Entity Type

Wedding Photography

Contact Information for Business Card

website, email, phone number

Font styles to use
Other font styles liked:
• Horizontes, Gotham

Colors

Designer to choose colors to be used in the design.

Requirements
Must have
• Website: www.mirelhatchway.com
• Phone: 418.629.5073
• Email: mirel@mirelhatchway.com
Nice to have
• I like the watercolor look but its not necessary. I like simple/earthy tones. Nothing too loud or distracting. Simple & feminine without being too girly. I like an approachable/soft feel.
• Instagram: www.instagram.com/mirelhatchwayphotography/
Should not have
• NO loud colors or design or pattern. I do not want a photo of a camera or lens or anything cheesy like that.

```html
<!DOCTYPE html>
<html lang="en">
<head>
<meta charset="utf-8">
<title>Mirel Hatchway – Business Card</title>
<link rel="stylesheet" href="https://fonts.googleapis.com/css2?family=Lato:wght@300;400&display=swap">
<style>
  :root {
    --backdrop: #5b5b5b;
    --card-white: #ffffff;
    --card-grey: #efefef;
    --sage: #a3b47b;
    --taupe: #dfc2a3;
    --peach: #f6dcbd;
    --cream: #fcefdf;
    --lime: #d0ec8d;
    --logo-ink: #8a7b72;
    --text-ink: #4a4543;
    --rule: #a49a93;
  }
  html, body {
    margin: 0;
    padding: 0;
    width: 1200px;
    height: 1200px;
    overflow: hidden;
    background: var(--backdrop);
    font-family: "Lato", Arial, sans-serif;
  }
  .canvas { position: relative; width: 1200px; height: 1200px; }
  .card { position: absolute; top: 310px; height: 594px; overflow: hidden; }
  .card-front { left: 234px; width: 364px; background: var(--card-white); }
  .card-back { left: 627px; width: 369px; background: var(--card-grey); }
  .tone-field {
    position: absolute;
    left: 0;
    right: 0;
    background: linear-gradient(135deg, var(--sage) 0%, var(--taupe) 35%, var(--peach) 60%, var(--cream) 78%, var(--lime) 100%);
  }
  .card-front .tone-field { top: 0; height: 465px; }
  .card-back .tone-field {
    top: 466px;
    height: 128px;
    background: linear-gradient(100deg, var(--sage) 0%, var(--taupe) 40%, var(--peach) 70%, var(--lime) 100%);
  }
  .wordmark {
    position: absolute;
    left: 0; right: 0;
    text-align: center;
    color: var(--logo-ink);
  }
  .wordmark-name {
    display: block;
    font-weight: 300;
    letter-spacing: 2px;
  }
  .wordmark-sub {
    display: block;
    font-weight: 400;
    font-size: 7.5px;
    letter-spacing: 5px;
    margin-top: 2px;
  }
  .card-front .wordmark { top: 498px; }
  .card-front .wordmark-name { font-size: 30px; }
  .card-back .wordmark { top: 124px; }
  .card-back .wordmark-name { font-size: 31px; }
  .rule {
    position: absolute;
    left: 113px;
    width: 150px;
    height: 1px;
    background: var(--rule);
  }
  .contact {
    position: absolute;
    left: 0; right: 0;
    top: 228px;
    text-align: center;
    color: var(--text-ink);
    font-size: 20px;
    line-height: 25px;
  }
  .contact p { margin: 0; }
  .social {
    position: absolute;
    left: 0; right: 0;
    top: 366px;
    text-align: center;
    color: var(--text-ink);
    font-size: 16px;
  }
</style>
</head>
<body>
<main class="canvas">
  <section class="card card-front" aria-label="Card front">
    <div class="tone-field" role="img" aria-label="Soft earthy colour field in sage, taupe, peach, cream and fresh green"></div>
    <div class="wordmark">
      <span class="wordmark-name">Mirel Hatchway</span>
      <span class="wordmark-sub">PHOTOGRAPHY</span>
    </div>
  </section>

  <section class="card card-back" aria-label="Card back">
    <div class="wordmark">
      <span class="wordmark-name">Mirel Hatchway</span>
      <span class="wordmark-sub">PHOTOGRAPHY</span>
    </div>
    <div class="rule" style="top:206px"></div>
    <div class="contact">
      <p>418.629.5073</p>
      <p>mirel@mirelhatchway.com</p>
      <p>www.mirelhatchway.com</p>
    </div>
    <div class="rule" style="top:335px"></div>
    <div class="social">lumigrid.net/mirelhatchwayphotography</div>
    <div class="tone-field" role="img" aria-label="Soft earthy colour band in sage, taupe, peach and fresh green"></div>
  </section>
</main>
</body>
</html>
```